we are an outdoor outlet in a country club that has a variety of outlets. The Club is called Meadowlark and is located in Cairo, Egypt. This garden menu will include cuisines from the Mediterranean, Asia and Texmex. we need a menu that is colorful and would fit an A3 size, back and front are to be used. Attached is the old menu currently in use (Garden Menu 2012.pdf is just for reference) and the new menu text for you to use is under the name Garden Menu Fall 2013
thank you.
Updates
Logo files have been uploaded for this project
Industry/Entity Type
Club
Look and feel
Each slider illustrates characteristics of the customer's brand and the style your logo design should communicate.

```html
<!DOCTYPE html>
<html lang="en">
<head>
<meta charset="utf-8">
<title>Garden Menu – Meadowlark</title>
<link rel="stylesheet" href="https://fonts.googleapis.com/css2?family=Montserrat:wght@700&family=Didact+Gothic&family=Quicksand:wght@700&family=Noto+Serif:wght@400;700&display=swap">
<style>
  :root {
    --paper: #f3e6c6;
    --paper-light: #f7eed8;
    --frame-green: #a9c93c;
    --brown: #6e4020;
    --orange: #e05a2a;
    --orange-text: #d0662f;
    --rust: #a8562a;
    --yellow: #f2d24a;
    --white: #ffffff;
    --sketch-light: #ece2cf;
    --sketch-mid: #ddcfb5;
  }
  * { box-sizing: border-box; margin: 0; padding: 0; }
  html, body { width: 848px; height: 1200px; overflow: hidden; }
  body { background: var(--paper); position: relative; font-family: "Didact Gothic", sans-serif; }

  .frame { position: absolute; left: 38px; top: 40px; width: 760px; height: 1102px; border: 3px solid var(--frame-green); }
  .header-band { position: absolute; left: 54px; top: 56px; width: 728px; height: 82px; background: var(--paper-light); }
  .menu-title { position: absolute; left: 95px; top: 74px; font-family: "Montserrat", sans-serif; font-weight: 700; font-size: 42px; color: var(--brown); letter-spacing: 0.5px; }
  .brand { position: absolute; left: 552px; top: 80px; display: flex; align-items: center; gap: 10px; }
  .brand-dot { width: 40px; height: 40px; border-radius: 50%; background: var(--frame-green); }
  .brand-name { font-family: "Didact Gothic", sans-serif; font-size: 28px; color: var(--brown); }

  .courses-box { position: absolute; left: 15px; top: 162px; width: 340px; height: 500px; background: var(--orange); border-radius: 16px; }
  .courses-box::after { content: ""; position: absolute; inset: 8px; border: 1.5px dashed rgba(255,255,255,0.7); border-radius: 12px; }

  .section-head { position: absolute; font-family: "Quicksand", sans-serif; font-weight: 700; letter-spacing: 3px; color: var(--brown); text-align: center; }
  .section-head.on-orange { color: var(--yellow); font-size: 24px; letter-spacing: 4px; }
  .section-rule { position: absolute; height: 1px; background: rgba(255,255,255,0.6); }
  .mark { position: absolute; width: 18px; height: 18px; border-radius: 50%; background: var(--yellow); }
  .mark.on-paper { background: var(--frame-green); }
  .section-note { position: absolute; font-family: "Noto Serif", serif; font-size: 9.5px; color: var(--brown); text-align: center; }

  .item { position: absolute; }
  .item-line { display: flex; justify-content: space-between; align-items: baseline; }
  .item-name { text-transform: uppercase; }
  .item-desc { font-family: "Noto Serif", serif; line-height: 1.32; }

  .main-item { left: 46px; width: 286px; }
  .main-item .item-line { font-size: 15px; color: var(--yellow); }
  .main-item .item-desc { font-size: 11.5px; color: var(--white); }

  .left-item { left: 100px; width: 283px; }
  .left-item .item-line { font-size: 12.5px; color: var(--brown); }
  .left-item .item-desc { font-size: 9.8px; color: var(--orange-text); }

  .right-item { left: 460px; width: 283px; }
  .right-item .item-line { font-size: 12.5px; color: var(--brown); }
  .right-item .item-desc { font-size: 9.8px; color: var(--rust); }

  .sauce-list { position: absolute; left: 46px; top: 584px; list-style: none; font-family: "Noto Serif", serif; font-size: 11.5px; color: var(--white); line-height: 1.4; }
  .box-tick { display: inline-block; width: 9px; height: 9px; border: 1px solid currentColor; margin-right: 5px; vertical-align: -1px; }

  .options { position: absolute; left: 460px; font-family: "Noto Serif", serif; font-size: 9.8px; color: var(--rust); }
  .options span { margin-right: 4px; }
  .options .box-tick { width: 8px; height: 8px; margin-right: 2px; }
  .opt-label { display: inline-block; width: 42px; color: var(--brown); }

  .corner-banner { position: absolute; left: 457px; top: 160px; width: 283px; height: 55px; background: var(--orange); color: var(--white); font-family: "Didact Gothic", sans-serif; font-size: 25px; line-height: 25px; text-align: right; padding: 3px 6px 0 0; }
  .corner-tab { position: absolute; left: 715px; top: 215px; width: 133px; height: 30px; }

  .art { position: absolute; border-radius: 50%; }
  .art-pizza { left: 350px; top: 172px; width: 115px; height: 92px; background: radial-gradient(ellipse, var(--sketch-mid) 0%, var(--sketch-light) 70%); }
  .art-plate { left: 210px; top: 545px; width: 280px; height: 130px; background: radial-gradient(ellipse, var(--sketch-light) 0%, var(--sketch-mid) 100%); }

  .tax-badge { position: absolute; left: 372px; top: 1067px; width: 96px; height: 96px; border-radius: 50%; background: var(--orange); color: var(--white); font-family: "Noto Serif", serif; font-weight: 700; font-size: 8.5px; line-height: 1.2; text-align: center; display: flex; align-items: center; justify-content: center; }
</style>
</head>
<body>
  <div class="frame"></div>
  <div class="header-band"></div>
  <h1 class="menu-title">GARDEN MENU</h1>
  <div class="brand"><span class="brand-dot"></span><span class="brand-name">Meadowlark</span></div>

  <section class="courses-box"></section>
  <h2 class="section-head on-orange" style="left:30px; top:183px; width:310px;">main courses</h2>
  <div class="section-rule" style="left:46px; top:226px; width:284px;"></div>
  <span class="mark" style="left:176px; top:217px;"></span>

  <div class="item main-item" style="top:244px;">
    <div class="item-line"><span class="item-name">Veal Parmeggiana</span><span>00.00</span></div>
    <p class="item-desc">Breaded veal escalope topped with<br>melted cheese and tomato sauce<br>served with Spaghetti</p>
  </div>
  <div class="item main-item" style="top:313px;">
    <div class="item-line"><span class="item-name">Chicken a la Francaise</span><span>00.00</span></div>
    <p class="item-desc">Pan fried chicken breast in a mushroom<br>cream sauce with vegetables white rice</p>
  </div>
  <div class="item main-item" style="top:369px;">
    <div class="item-line"><span class="item-name">Grilled Salmon</span><span>00.00</span></div>
    <p class="item-desc">Salmon steak charcoal grilled<br>with avocado tomato relish<br>and creamy mushroom risotto</p>
  </div>
  <div class="item main-item" style="top:439px;">
    <div class="item-line"><span class="item-name">Moroccan Chicken</span><span>00.00</span></div>
    <p class="item-desc">Chicken cubes simmered with spices<br>and olives served with tomato rice</p>
  </div>
  <div class="item main-item" style="top:495px;">
    <div class="item-line"><span class="item-name">Filet</span><span>00.00</span></div>
    <p class="item-desc">Tender filet grilled to your liking<br>served with mashed potato<br>and creamed spinach</p>
  </div>
  <div class="item main-item" style="top:564px;">
    <div class="item-line"><span class="item-name">Choice of Sauces</span></div>
  </div>
  <ul class="sauce-list">
    <li><span class="box-tick"></span>Brown Mushroom</li>
    <li><span class="box-tick"></span>Green Peppercorn</li>
    <li><span class="box-tick"></span>Gorgonzola</li>
  </ul>

  <div class="art art-pizza" role="img" aria-label="Sketch of pizza slice with tomatoes and garlic"></div>
  <div class="art art-plate" role="img" aria-label="Sketch of plated dish with fork and knife"></div>

  <h2 class="section-head" style="left:140px; top:682px; width:200px; font-size:20px;">salads</h2>
  <span class="mark on-paper" style="left:231px; top:709px;"></span>
  <div class="item left-item" style="top:727px;">
    <div class="item-line"><span class="item-name">Caprese</span><span>00.00</span></div>
    <p class="item-desc">Buffalo mozzarella and sliced tomato<br>with a balsamic vinaigrette</p>
  </div>
  <div class="item left-item" style="top:773px;">
    <div class="item-line"><span class="item-name">Rocket Apple</span><span>00.00</span></div>
    <p class="item-desc">Rocket leaves with gorgonzola, croutons,<br>and strawberry vinaigrette</p>
  </div>
  <div class="item left-item" style="top:819px;">
    <div class="item-line"><span class="item-name">French Riviera Nicoise</span><span>00.00</span></div>
    <p class="item-desc">Lettuce, egg, tomato, tuna, olives, onion,<br>celery, radish, bell pepper in a French vinaigrette</p>
  </div>
  <div class="item left-item" style="top:865px;">
    <div class="item-line"><span class="item-name">Folle</span><span>00.00</span></div>
    <p class="item-desc">Mixed greens with crab sticks, mushroom,<br>corn, cherry tomato in a mango vinaigrette</p>
  </div>

  <h2 class="section-head" style="left:140px; top:918px; width:200px; font-size:20px;">soups</h2>
  <span class="mark on-paper" style="left:231px; top:944px;"></span>
  <div class="item left-item" style="top:962px;">
    <div class="item-line"><span class="item-name">Tomato Basil</span><span>00.00</span></div>
    <p class="item-desc">Simmered tomato soup finished with<br>fresh basil and cream</p>
  </div>
  <div class="item left-item" style="top:1008px;">
    <div class="item-line"><span class="item-name">Chicken Cream</span><span>00.00</span></div>
    <p class="item-desc">Chicken broth with roasted chicken cubes,<br>pine nuts, and cream</p>
  </div>
  <div class="item left-item" style="top:1054px;">
    <div class="item-line"><span class="item-name">Moroccan Harira</span><span>00.00</span></div>
    <p class="item-desc">Vegetable broth with fresh tomato,<br>chickpeas, lentil, cilantro, and diced lamb</p>
  </div>

  <svg class="corner-tab" viewBox="0 0 133 30" aria-hidden="true">
    <polygon points="0,0 133,0 133,30 25,30" fill="#a9c93c"/>
    <polygon points="0,0 25,0 0,30" fill="#8a3a18"/>
  </svg>
  <div class="corner-banner">MEDITERRANEAN<br>CORNER</div>

  <h2 class="section-head" style="left:480px; top:228px; width:240px; font-size:19px;">pizza &amp; pasta</h2>
  <span class="mark on-paper" style="left:591px; top:254px;"></span>
  <div class="item right-item" style="top:272px;">
    <div class="item-line"><span class="item-name">Pizza Margarita <small style="font-size:9.5px; text-transform:none;">(Choose your toppings)</small></span><span>00.00</span></div>
  </div>
  <div class="options" style="top:290px;">
    <span><i class="box-tick"></i>Bell Peppers</span><span><i class="box-tick"></i>Olives</span><span><i class="box-tick"></i>Tomato</span><span><i class="box-tick"></i>Onion</span><span><i class="box-tick"></i>Mushroom</span>
  </div>
  <div class="options" style="top:305px;">
    <span><i class="box-tick"></i>Chicken</span><span><i class="box-tick"></i>Tuna</span><span><i class="box-tick"></i>Pepperoni</span><span><i class="box-tick"></i>Smoked Salmon</span><span><i class="box-tick"></i>Shrimps</span>
  </div>
  <div class="item right-item" style="top:326px;">
    <div class="item-line"><span class="item-name">Create Your Own Pasta</span><span>00.00</span></div>
  </div>
  <div class="options" style="top:345px;">
    <span class="opt-label">TYPE</span><span><i class="box-tick"></i>Spaghetti</span>&nbsp;&nbsp;<span><i class="box-tick"></i>Tagliatelle</span>&nbsp;<span><i class="box-tick"></i>Penne</span>
  </div>
  <div class="options" style="top:359px;">
    <span class="opt-label">SAUCES</span><span><i class="box-tick"></i>Napolitana</span><span><i class="box-tick"></i>Bolognese</span><span><i class="box-tick"></i>Alfredo</span>
  </div>
  <div class="item right-item" style="top:382px;">
    <div class="item-line"><span class="item-name">Lasagna</span><span>00.00</span></div>
  </div>

  <h2 class="section-head" style="left:480px; top:407px; width:240px; font-size:19px;">sandwiches</h2>
  <p class="section-note" style="left:480px; top:429px; width:240px;">(Served with french fries or garden salad)</p>
  <span class="mark on-paper" style="left:591px; top:443px;"></span>
  <div class="item right-item" style="top:464px;"><div class="item-line"><span class="item-name">Beef or Chicken Shawerma</span><span>00.00</span></div></div>
  <div class="item right-item" style="top:490px;"><div class="item-line"><span class="item-name">Grilled Kofta</span><span>00.00</span></div></div>
  <div class="item right-item" style="top:516px;">
    <div class="item-line"><span class="item-name">Greek Lamb Gyro</span><span>00.00</span></div>
    <p class="item-desc">in pita bread with Tzatziki</p>
  </div>
  <div class="item right-item" style="top:552px;">
    <div class="item-line"><span class="item-name">Club Sandwich</span><span>00.00</span></div>
    <p class="item-desc">with smoked beef, turkey, egg</p>
  </div>

  <h2 class="section-head" style="left:480px; top:589px; width:240px; font-size:19px;">appetizers</h2>
  <span class="mark on-paper" style="left:591px; top:613px;"></span>
  <div class="item right-item" style="top:632px;">
    <div class="item-line"><span class="item-name">Salmon Tartare</span><span>00.00</span></div>
    <p class="item-desc">Seasoned with lemon juice, garlic,<br>and crushed black pepper</p>
  </div>
  <div class="item right-item" style="top:679px;">
    <div class="item-line"><span class="item-name">Roasted Eggplant Rolls</span><span>00.00</span></div>
    <p class="item-desc">With herbed ricotta cheese and pine nuts</p>
  </div>
  <div class="item right-item" style="top:714px;">
    <div class="item-line"><span class="item-name">Falafel in Mini Pita</span><span>00.00</span></div>
    <p class="item-desc">Served with tehina and oriental salsa</p>
  </div>
  <div class="item right-item" style="top:749px;">
    <div class="item-line"><span class="item-name">Mankousha</span><span>00.00</span></div>
    <p class="item-desc">With thyme and olive oil</p>
  </div>
  <div class="item right-item" style="top:784px;">
    <div class="item-line"><span class="item-name">Fried Kobeba</span><span>00.00</span></div>
    <p class="item-desc">With minced meat, spices, and pine nuts</p>
  </div>
  <div class="item right-item" style="top:819px;">
    <div class="item-line"><span class="item-name">Fried Calamari a la Romana</span><span>00.00</span></div>
    <p class="item-desc">Served with aioli</p>
  </div>
  <div class="item right-item" style="top:854px;">
    <div class="item-line"><span class="item-name">Samboussek</span><span>00.00</span></div>
    <p class="item-desc">With herbed white cheese and mint</p>
  </div>
  <div class="item right-item" style="top:889px;">
    <div class="item-line"><span class="item-name">Oriental Sausage Sautéed</span><span>00.00</span></div>
    <p class="item-desc">With garlic and onion</p>
  </div>
  <div class="item right-item" style="top:924px;">
    <div class="item-line"><span class="item-name">Mini Vine Leaves</span><span>00.00</span></div>
    <p class="item-desc">With a yoghurt dip</p>
  </div>
  <div class="item right-item" style="top:959px;">
    <div class="item-line"><span class="item-name">Fatouch</span><span>00.00</span></div>
    <p class="item-desc">With a pomegranate syrup dressing</p>
  </div>
  <div class="item right-item" style="top:994px;">
    <div class="item-line"><span class="item-name">Hummus</span><span>00.00</span></div>
    <p class="item-desc">Seasoned with lemon juice, garlic, and olive oil</p>
  </div>
  <div class="item right-item" style="top:1029px;">
    <div class="item-line"><span class="item-name">White Cheese</span><span>00.00</span></div>
    <p class="item-desc">With diced tomato, thyme, and olive oil</p>
  </div>
  <div class="item right-item" style="top:1064px;">
    <div class="item-line"><span class="item-name">Tehina</span><span>00.00</span></div>
    <p class="item-desc">Seasoned with cumin, lemon juice, and garlic</p>
  </div>

  <div class="tax-badge"><p>PRICES ARE<br>SUBJECT TO<br>12% SERVICE<br>CHARGE &amp;<br>10% SALES TAX</p></div>
</body>
</html>
```